Book Title: “Faith: Road of Endless Grace” Please see the attachment “Text on the cover”.

Book Cover Design Instructions: This book is meant for people of all religions and nationalities. Therefore, on the cover, there should be no mosque or an object specific to any religion. The primary emphasis should be on the "unconditional love of God." Therefore, use universal symbols of love. The second priority themes could be Sufism, Peace, and self-improvement. Rest is your imagination. Please also see the attachment: 'Book description and author's Bio.'
This book has the potential to be a best seller. Please do a good job.
What Book Cover Formats are required: A designer should submit cover designs in three formats: (1) eBook, (2) Paperback, and (3) Hardback. These books will be published on Borvex QPL.
Format requirements for eBooks are available from: https://qpl.borvex.example/en_US/help/topic/R731928457.
You can find paperback and hardback cover measurements from: https://qpl.borvex.example/en_US/cover-calculator
• To complete the project, all three formats should be accepted by Borvex QPL.
• The book interior trim size is 6.14 X 9.21 inches.
• Interior Type: Premium color.
• No bleed.
• I do not upload barcode. So, the back cover should have room for Borvex to print the barcode.
• Number of pages 126.
Compensation for the designer: After selecting one designer, I will increase the amount by $200 on Artvelle to compensate for three deliverables.
Follow-up of the Project:
After the book is published, I may need minor revisions. For example, the number of pages may change. Therefore, I will need the same design in revised sizes. In that case, I will pay $25 for each revision. For example, if the number of pages changes, I will need a different spine for paperback and hardback, then I will pay the artist $25 + $25 = $50 for both designs.
List of Enclosers:
1. Text on the cover.
2. Book description and author's Bio for the back cover.
3. Later, I will upload my picture for the book's back cover.

Target Market(s)

Any adult

Industry/Entity Type

Any industry

Requirements
Must have
• Three Deliverables

```html
<!DOCTYPE html>
<html lang="en">
<head>
<meta charset="utf-8">
<title>Faith: Road of Endless Grace — Book Cover</title>
<link rel="stylesheet" href="https://fonts.googleapis.com/css2?family=Montserrat:wght@500;600;700&display=swap">
<style>
  :root {
    --page: #ffffff;
    --cover-blue: #04519d;
    --sky-deep: #3a86c6;
    --sky-mid: #79b3dd;
    --sky-light: #b9d7ec;
    --cloud: #e2edf5;
    --wall: #c9a98c;
    --wall-dark: #b38f73;
    --ink-light: #ffffff;
    --heart: rgba(255, 255, 255, 0.9);
    --heart-glow: rgba(255, 255, 255, 0.35);
  }
  * { box-sizing: border-box; margin: 0; padding: 0; }
  html, body {
    width: 1200px;
    height: 1200px;
    overflow: hidden;
    background: var(--page);
    font-family: "Montserrat", sans-serif;
  }
  .cover {
    position: absolute;
    left: 223px;
    top: 32px;
    width: 764px;
    height: 1145px;
    background: var(--cover-blue);
    overflow: hidden;
  }
  .cover-sky {
    position: absolute;
    left: 0;
    top: 400px;
    width: 100%;
    height: 660px;
    background: linear-gradient(
      to bottom,
      var(--cover-blue) 0%,
      var(--sky-deep) 16%,
      var(--sky-mid) 40%,
      var(--sky-light) 68%,
      var(--cloud) 86%,
      var(--wall) 90%,
      var(--wall-dark) 100%
    );
  }
  .love-symbol {
    position: absolute;
    left: 272px;
    top: 640px;
    width: 220px;
    height: 198px;
    filter: drop-shadow(0 0 24px var(--heart-glow));
  }
  .title-main {
    position: absolute;
    left: 0;
    top: 37px;
    width: 100%;
    text-align: center;
    color: var(--ink-light);
    font-weight: 600;
    font-size: 212px;
    line-height: 1;
  }
  .title-sub {
    position: absolute;
    left: 0;
    top: 239px;
    width: 100%;
    text-align: center;
    color: var(--ink-light);
    font-weight: 600;
    font-size: 56px;
    line-height: 1;
  }
  .tagline {
    position: absolute;
    left: 0;
    top: 340px;
    width: 100%;
    text-align: center;
    color: var(--ink-light);
    font-weight: 600;
    font-size: 31px;
    line-height: 42px;
  }
  .author-band {
    position: absolute;
    left: 0;
    bottom: 0;
    width: 100%;
    height: 85px;
    background: var(--cover-blue);
    display: flex;
    align-items: center;
    justify-content: center;
  }
  .author-name {
    color: var(--ink-light);
    font-weight: 600;
    font-size: 42px;
    letter-spacing: 1.5px;
  }
</style>
</head>
<body>
  <div class="cover">
    <div class="cover-sky" role="img" aria-label="Open blue sky with soft clouds above a warm sandstone horizon"></div>
    <svg class="love-symbol" viewBox="0 0 100 90" role="img" aria-label="Heart, a universal symbol of love">
      <path d="M50 86 C20 62 4 44 4 26 C4 12 15 4 27 4 C38 4 46 11 50 20 C54 11 62 4 73 4 C85 4 96 12 96 26 C96 44 80 62 50 86 Z" fill="var(--heart)"/>
    </svg>
    <h1 class="title-main">FAITH</h1>
    <p class="title-sub">Road of Endless Grace</p>
    <p class="tagline">Guide to<br>Cultivating Inner Peace<br>and Mindful Living</p>
    <div class="author-band">
      <p class="author-name">DR. IRAVAN SOLEH</p>
    </div>
  </div>
</body>
</html>
```